Wellness Coach/Personal trainer needs wordpress site/blog with ecommerce capable membership area

We need a WordPress design for FitPennyCoach.com. This is a blog about wellness, weight loss, and health related topics. Design logo will be provided to the winner.

A great site with a design that we would like to emulate are http://qv4.example. The design should be simple, clean, unique, fun, and distinctive. Above all, it should be highly readable and easy to navigate.

These are the specific sections/categories of the blog that should be included and incorporated into the design SEE BELOW.

Thanks in advance for your consideration
Updates

Project Deadline Extended
Reason: I have extended the deadline to evaluate more designs from other pros

Hello all, Please take a minute to review the requirements for this project and please make sure you are capable of meeting ALL the requirements. As you already know I will be making a decision very shortly on whose design I will be moving forward with, if there are any last minute submissions now is the time. Thank you for your time.

Target Market(s)

90 % women 10 % men my clients are usually professionals who value their appearance, health, longevity and time.

Industry/Entity Type

Personal Trainer

Font styles to use
Serif

Colors
886aae
ffcf3e

Requirements
Must have
• Requirements

- start losing weight today.... 555 207 9184 (first line)
- visuals/images and backgrounds to give the idea of wellness, weight loss, healthy living, etc
- navigation menu - home, who we are, what we do, who we serve, blog, contact, members area

1) slider element at top below navigation menu
2) slider element near bottom of page will have testimonials
3) contact form/inquiry form (one page)
4) will provide wellness logo (to give credibility)
5) color scheme purple, gold and white
6) membership area
7) fb, tw, youtube icons
8) footer area - In the footer, there will be smaller company logo, copyright,
disclaimer, privacy policy, terms n conditions, verse of day, and contact info, Phone: (555) 207-9184
Email: support@...
Address:
9) use dummy content/graphic as they will be replaced by real content (the winner will provide instruction on how to make changes to all text and changing graphics)
9) ecommerce enabled / newsletter signup area

```html
<!DOCTYPE html>
<html lang="en">
<head>
<meta charset="utf-8">
<title>FitPenny Coach – Wellness Blog</title>
<link href="https://fonts.googleapis.com/css2?family=Open+Sans:ital,wght@0,400;0,600;0,700;1,400&family=PT+Serif:ital,wght@0,400;0,700;1,400&display=swap" rel="stylesheet">
<style>
:root{
  --purple:#7d5d8c;
  --purple-dark:#6b4e79;
  --gold:#d4a00a;
  --ink:#2d2d2d;
  --text:#555;
  --muted:#777;
  --white:#fff;
  --band:#3b3b3b;
}
*{margin:0;padding:0;box-sizing:border-box}
html,body{width:1200px;height:3114px;overflow:hidden}
body{position:relative;background:var(--white);font-family:"Open Sans",Arial,sans-serif;color:var(--text)}
.abs{position:absolute}

/* header */
.site-header{left:0;top:0;width:1200px;height:73px;background:var(--purple)}
.brand{left:33px;top:14px;display:flex;align-items:center;gap:12px;color:var(--white);font-family:"PT Serif",Georgia,serif;font-size:30px;white-space:nowrap}
.brand-dot{width:44px;height:44px;border-radius:50%;background:var(--white);opacity:.9}
.main-nav{right:32px;top:0;height:73px;display:flex;align-items:center;gap:48px}
.main-nav a{color:var(--white);text-decoration:none;font-size:14px}

/* hero slider */
.hero{left:0;top:73px;width:1200px;height:583px;background:radial-gradient(ellipse at 55% 40%,#fbfbfb 0%,#ececec 60%,#dedede 100%);overflow:hidden}
.hero-photo{left:353px;top:20px;width:780px;height:560px;background:radial-gradient(ellipse at 62% 55%,rgba(160,150,156,.55) 0%,rgba(190,184,188,.35) 40%,rgba(230,230,230,0) 72%)}
.hero-title{left:139px;top:136px;font-size:37px;font-weight:700;color:var(--purple);letter-spacing:.5px}
.hero-sub{left:139px;top:187px;width:400px;font-size:23px;font-weight:600;color:var(--ink);line-height:37px}
.hero-text{left:139px;top:268px;width:360px;font-size:12.5px;line-height:24px;color:#333}
.btn{display:flex;align-items:center;justify-content:center;color:var(--white);font-weight:700;text-transform:uppercase;text-decoration:none;border-radius:3px;white-space:nowrap}
.btn-purple{background:var(--purple);box-shadow:0 4px 0 #5a4266}
.btn-gold{background:var(--gold);box-shadow:0 4px 0 #8f6c04}
.hero-btn{left:139px;top:363px;width:285px;height:58px;font-size:15px}
.call-badge{left:569px;top:124px;width:212px;height:212px;border-radius:50%;background:var(--gold);border:5px solid #f4e6b8;color:var(--white);text-align:center;font-family:"PT Serif",Georgia,serif;display:flex;flex-direction:column;align-items:center;justify-content:center}
.call-badge .start{font-size:27px;font-weight:700;font-family:"Open Sans",Arial,sans-serif}
.call-badge .line{font-size:26px;font-style:italic;line-height:30px}
.call-badge .phone{margin-top:12px;font-family:"Open Sans",Arial,sans-serif;font-weight:700;font-size:22px}
.arrow{top:250px;width:24px;height:70px}

/* testimonial band */
.testimonials{left:0;top:656px;width:1200px;height:135px;background:var(--band)}
.avatar{left:170px;top:25px;width:92px;height:92px;border-radius:50%;background:linear-gradient(#d9b79b,#b88a6c);border:3px solid #fff}
.quote{left:322px;top:33px;width:650px;font-size:12px;font-style:italic;line-height:24px;color:#b9b9b9}
.quote-mark{font-family:"PT Serif",Georgia,serif;font-size:26px;color:#999}
.quote-author{left:322px;top:88px;font-size:11px;color:#fff;text-transform:uppercase}
.quote-author em{text-transform:none;font-size:10px}
.slide-ctrl{left:950px;top:92px;font-size:14px;color:#aaa;letter-spacing:10px}

/* section heads */
.section-title{left:0;width:1200px;text-align:center;font-size:25px;font-weight:700;color:var(--ink)}
.section-lead{left:0;width:1200px;text-align:center;font-size:16px;color:var(--text)}

/* services */
.service{width:300px;text-align:center}
.service-icon{width:146px;height:146px;margin:0 auto;border-radius:50%;background:var(--purple);box-shadow:0 6px 0 #5a4266;display:flex;align-items:center;justify-content:center}
.service h3{margin-top:27px;font-size:18px;color:var(--ink);font-weight:700}
.service p{margin:16px auto 0;width:250px;font-size:12px;line-height:25px;color:var(--muted)}
.service .btn{margin:22px auto 0;width:133px;height:42px;font-size:12px;font-weight:600}

/* members band */
.members{left:0;top:1376px;width:1200px;height:378px;background:linear-gradient(180deg,#2c2628 0%,#3a3234 50%,#221e20 100%)}
.members-text{left:0;top:79px;width:1200px;text-align:center;color:var(--white);font-weight:700;font-size:24px;line-height:38px}
.members-btn{top:175px;width:247px;height:58px;font-size:16px}
.call-line{left:0;top:263px;width:1200px;text-align:center;font-family:"PT Serif",Georgia,serif;font-size:37px;color:var(--white)}
.call-line span{color:var(--gold)}

/* posts */
.post{width:260px}
.post-img{height:195px}
.post h4{margin-top:16px;font-size:17px;color:var(--purple);font-weight:700}
.post .date{margin-top:6px;font-size:11px;font-style:italic;color:#333}
.post p{margin-top:9px;font-size:11px;line-height:21px;color:var(--muted)}
.more-btn{left:477px;top:2607px;width:245px;height:57px;font-size:16px}

/* footer */
.site-footer{left:0;top:2713px;width:1200px;height:339px;background:var(--purple)}
.foot-col{top:52px;color:var(--white)}
.foot-col h5{font-size:19px;font-weight:400;margin-bottom:12px}
.foot-col li{list-style:none;font-size:11px;line-height:21.6px;white-space:nowrap}
.field{width:212px;height:29px;border:1px solid #c7b6cf;background:var(--purple-dark);font-size:10px;padding:7px 8px;margin-bottom:12px;color:#eee}
.field.msg{height:44px}
.submit{width:131px;height:33px;background:#5c4268;font-size:10px;color:#fff;display:flex;align-items:center;justify-content:center}
.foot-brand{left:820px;top:190px;width:220px;text-align:center;color:#fff;font-family:"PT Serif",Georgia,serif;font-size:26px;white-space:nowrap}
.foot-brand .dot{width:44px;height:44px;border-radius:50%;background:#fff;margin:0 auto 10px;opacity:.9}
.bottom-bar{left:0;top:3052px;width:1200px;height:62px;background:var(--purple-dark)}
.copy{left:172px;top:22px;font-size:11px;color:#fff}
.social{top:17px;width:28px;height:28px;border-radius:50%;background:#fff}
</style>
</head>
<body>

<header class="site-header abs">
  <div class="brand abs"><span class="brand-dot"></span>FitPenny Coach</div>
  <nav class="main-nav abs">
    <a href="#">Home</a><a href="#">who we are?</a><a href="#">what we do?</a><a href="#">who we serve?</a><a href="#">Contact</a><a href="#">Blog</a><a href="#">Members</a>
  </nav>
</header>

<section class="hero abs">
  <div class="hero-photo abs" role="img" aria-label="Woman in a yoga stretch pose on a light background"></div>
  <h1 class="hero-title abs">WE ARE A BLOG</h1>
  <h2 class="hero-sub abs">ABOUT WELLNESS WEIGHT LOSS, AND HEALTH</h2>
  <p class="hero-text abs">Lorem Ipsum is simply dummy text of the printing and typesetting industry. Lorem Ipsum has been the industry's standard dummy text ever since the 1500s</p>
  <a class="btn btn-purple hero-btn abs" href="#">Click here for more info</a>
  <div class="call-badge abs">
    <div class="start">Start</div>
    <div class="line">losing weight</div>
    <div class="line">today....</div>
    <div class="phone">555 207 9184</div>
  </div>
  <svg class="arrow abs" style="left:62px" viewBox="0 0 24 70"><polyline points="20,2 4,35 20,68" fill="none" stroke="#cfcfcf" stroke-width="2"/></svg>
  <svg class="arrow abs" style="left:1126px" viewBox="0 0 24 70"><polyline points="4,2 20,35 4,68" fill="none" stroke="#cfcfcf" stroke-width="2"/></svg>
</section>

<section class="testimonials abs">
  <div class="avatar abs" role="img" aria-label="Client portrait"></div>
  <span class="quote-mark abs" style="left:288px;top:20px">&ldquo;</span>
  <p class="quote abs">Lorem Ipsum is simply dummy text of the printing and typesetting industry. Lorem Ipsum has been the industry's standard<br>Lorem Ipsum is simply dummy text of the printing and typesetting industry...</p>
  <p class="quote-author abs">Lena Marsh <em>Marketing executive</em></p>
  <span class="quote-mark abs" style="left:982px;top:58px">&rdquo;</span>
  <span class="slide-ctrl abs">&lsaquo;&rsaquo;</span>
</section>

<h2 class="section-title abs" style="top:852px">FitPenny Coach Services</h2>
<p class="section-lead abs" style="top:898px">Lorem Ipsum is simply dummy text of the printing and typesetting industry.</p>

<div class="service abs" style="left:161px;top:969px">
  <div class="service-icon">
    <svg width="66" height="50" viewBox="0 0 66 50" fill="#fff"><circle cx="33" cy="12" r="9"/><path d="M18 46c0-12 7-20 15-20s15 8 15 20z"/><circle cx="13" cy="18" r="7"/><path d="M0 46c0-9 5-15 13-15 3 0 5 1 6 2-3 4-4 8-4 13z"/><circle cx="53" cy="18" r="7"/><path d="M66 46c0-9-5-15-13-15-3 0-5 1-6 2 3 4 4 8 4 13z"/></svg>
  </div>
  <h3>Who we are?</h3>
  <p>Lorem Ipsum is simply dummy text of the printing and typesetting industry. Lorem Ipsum has been the industry's standard .</p>
  <a class="btn btn-purple" href="#">Click here</a>
</div>
<div class="service abs" style="left:452px;top:969px">
  <div class="service-icon">
    <svg width="40" height="66" viewBox="0 0 40 66"><path d="M6 16C6 7 12 3 20 3s14 5 14 13c0 10-12 12-12 24v4" fill="none" stroke="#fff" stroke-width="9" stroke-linecap="round"/><circle cx="22" cy="58" r="6" fill="#fff"/></svg>
  </div>
  <h3>What we do?</h3>
  <p>Lorem Ipsum is simply dummy text of the printing and typesetting industry. Lorem Ipsum has been the industry's standard..</p>
  <a class="btn btn-purple" href="#">Click here</a>
</div>
<div class="service abs" style="left:751px;top:969px">
  <div class="service-icon">
    <svg width="70" height="44" viewBox="0 0 70 44" fill="#fff"><path d="M0 8h12l10 6 8-4h8l10 8 10-10h12v18h-8L48 40c-3 3-7 3-9 0l-4 2c-3 1-5-1-6-3l-3 1c-3 0-4-2-4-4l-2 0c-3 0-4-3-3-5L8 26H0z"/></svg>
  </div>
  <h3>Who we serve?</h3>
  <p>Lorem Ipsum is simply dummy text of the printing and typesetting industry. Lorem Ipsum has been the industry's standard..</p>
  <a class="btn btn-purple" href="#">Click here</a>
</div>

<section class="members abs" role="img" aria-label="Mosaic of member portrait photos, darkened">
  <p class="members-text abs">Lorem Ipsum is simply dummy text of the printing and typesetting<br>industry. Lorem Ipsum has been the industry's...</p>
  <a class="btn btn-gold members-btn abs" style="left:336px" href="#">Members login</a>
  <a class="btn btn-gold members-btn abs" style="left:619px" href="#">Members register</a>
  <p class="call-line abs">( or ) Call Us : <span>555 207 9184</span></p>
</section>

<h2 class="section-title abs" style="top:1809px">Recent Posts</h2>
<p class="section-lead abs" style="top:1855px">Lorem Ipsum is simply dummy text of the printing and typesetting industry.</p>

<article class="post abs" style="left:172px;top:1918px"><div class="post-img" role="img" aria-label="Woman meditating by the sea" style="background:linear-gradient(180deg,#9fb7c4,#5d7b8c 60%,#4f5a5c)"></div><h4>Lorem ipsum is a dummy</h4><p class="date">Posted on 27 march 2014</p><p>Lorem Ipsum is simply dummy text of the printing and typesetting industry.</p></article>
<article class="post abs" style="left:469px;top:1918px"><div class="post-img" role="img" aria-label="Cyclist riding on a grassy trail" style="background:linear-gradient(180deg,#e9e3b4,#a7ae5e 55%,#5c6b2a)"></div><h4>Lorem ipsum is a dummy</h4><p class="date">Posted on 27 march 2014</p><p>Lorem Ipsum is simply dummy text of the printing and typesetting industry.</p></article>
<article class="post abs" style="left:768px;top:1918px"><div class="post-img" role="img" aria-label="Woman blowing a dandelion in a meadow" style="background:linear-gradient(135deg,#6f8e3a,#a6b65a 50%,#4a5f24)"></div><h4>Lorem ipsum is a dummy</h4><p class="date">Posted on 27 march 2014</p><p>Lorem Ipsum is simply dummy text of the printing and typesetting industry.</p></article>
<article class="post abs" style="left:172px;top:2261px"><div class="post-img" role="img" aria-label="Family running across a field" style="background:linear-gradient(180deg,#7fb6e3,#b9d6ea 50%,#6c9c3c)"></div><h4>Lorem ipsum is a dummy</h4><p class="date">Posted on 27 march 2014</p><p>Lorem Ipsum is simply dummy text of the printing and typesetting industry.</p></article>
<article class="post abs" style="left:469px;top:2261px"><div class="post-img" role="img" aria-label="Woman relaxing on the beach" style="background:linear-gradient(180deg,#9fc7d6,#6aa3b3 50%,#b1a99a)"></div><h4>Lorem ipsum is a dummy</h4><p class="date">Posted on 27 march 2014</p><p>Lorem Ipsum is simply dummy text of the printing and typesetting industry.</p></article>
<article class="post abs" style="left:768px;top:2261px"><div class="post-img" role="img" aria-label="Father teaching child to ride a bike on the beach" style="background:linear-gradient(180deg,#bcd8ea,#8fb8cf 55%,#d8c9a8)"></div><h4>Lorem ipsum is a dummy</h4><p class="date">Posted on 27 march 2014</p><p>Lorem Ipsum is simply dummy text of the printing and typesetting industry.</p></article>

<a class="btn btn-gold more-btn abs" href="#">View more posts</a>

<footer class="site-footer abs">
  <div class="foot-col abs" style="left:176px"><h5>Welcome</h5><ul><li>Home</li><li>Who we are</li><li>What we do</li><li>Who we serve</li><li>Contact</li><li>Blog</li><li>Members</li></ul></div>
  <div class="foot-col abs" style="left:365px"><h5>Information</h5><ul><li>Copyright</li><li>Disclaimer</li><li>Privacy policy</li><li>Terms n conditions</li><li>Verse of day,</li></ul></div>
  <div class="foot-col abs" style="left:546px"><h5>Contact form</h5>
    <div class="field">Name :</div><div class="field">Email :</div><div class="field">Phone :</div><div class="field msg">Message :</div>
    <div class="submit">SUBMIT</div>
  </div>
  <div class="foot-col abs" style="left:845px"><h5>Contact Info</h5><ul><li>Phone: (555) 207-9184</li><li>Email: support@fitpennycoach.com</li><li>120 Street name, state name,</li><li>country name</li></ul></div>
  <div class="foot-brand abs"><div class="dot"></div>FitPenny Coach</div>
</footer>

<div class="bottom-bar abs">
  <p class="copy abs">Copyright © 2014. FitPenny Coach. All rights reserved.</p>
  <span class="social abs" style="left:924px" aria-label="Social link one"></span>
  <span class="social abs" style="left:962px" aria-label="Social link two"></span>
  <span class="social abs" style="left:997px" aria-label="Social link three"></span>
</div>

</body>
</html>
```